Velmora Crest Cosmetic Mirror suitable for purse or travel

Design a small packaging box, completed size 75mm x 75mm x 10mm. Suitable for small cosmetic mirror.
External colors of mirrors are silver, black and rose gold. Mirror is dual - 1 x magnification and 3x magnification. Packaging box should be suitable for all three colours.
Card weight 350gsm or similar, gloss finish by preference.
Brand name is Velmora Crest and will include textiles, homewares and beauty accessories.

Target Market(s)

US Market, all age range, primarily women

Industry/Entity Type

Beauty Aid

Font styles to use
Other font styles liked:
• Salaryman

Requirements
Must have
• My logo - Velmora Crest, barcode placed on rear of box at bottom right corner, country of origin

```html
<!DOCTYPE html>
<html lang="en">
<head>
<meta charset="utf-8">
<title>Velmora Crest – Dual-Sided Makeup Mirror Box</title>
<link href="https://fonts.googleapis.com/css2?family=Questrial&display=swap" rel="stylesheet">
<style>
  :root {
    --stage: #f1f1f1;
    --board: #060606;
    --gold: #d9b441;
    --ink: #ffffff;
  }
  * { margin: 0; padding: 0; box-sizing: border-box; }
  html, body {
    width: 825px;
    height: 1200px;
    overflow: hidden;
    background: var(--stage);
  }
  body {
    font-family: "Questrial", "Century Gothic", sans-serif;
    position: relative;
  }
  .front-panel {
    position: absolute;
    left: 112px;
    top: 110px;
    width: 600px;
    height: 600px;
    background: var(--board);
    color: var(--ink);
    text-align: center;
  }
  .brand-name {
    position: absolute;
    left: 0;
    right: 0;
    top: 180px;
    color: var(--gold);
    font-size: 22px;
    line-height: 1;
    letter-spacing: 0.5px;
    text-transform: uppercase;
  }
  .product-title {
    position: absolute;
    left: 0;
    right: 0;
    top: 356px;
    font-weight: 400;
    font-size: 36px;
    line-height: 1;
    letter-spacing: 0.5px;
  }
  .product-subtitle {
    position: absolute;
    left: 0;
    right: 0;
    top: 398px;
    font-size: 12.5px;
    line-height: 1;
    letter-spacing: 0.4px;
  }
  .magnification {
    position: absolute;
    left: 0;
    right: 0;
    top: 448px;
    font-size: 15px;
    line-height: 1;
  }
  .colour-variant {
    position: absolute;
    left: 0;
    right: 0;
    top: 510px;
    font-size: 13px;
    line-height: 1;
    letter-spacing: 0.4px;
  }
  .spine-panel {
    position: absolute;
    left: 112px;
    top: 780px;
    width: 600px;
    height: 80px;
    background: var(--board);
    color: var(--ink);
    display: flex;
    align-items: center;
    padding: 0 36px;
  }
  .spine-title { line-height: 1; }
  .spine-title strong {
    display: block;
    font-weight: 400;
    font-size: 24px;
  }
  .spine-title span {
    display: block;
    font-size: 9px;
    margin-top: 5px;
    letter-spacing: 0.3px;
  }
  .spine-brand {
    margin-left: auto;
    color: var(--gold);
    font-size: 20px;
    line-height: 1;
    text-transform: uppercase;
    letter-spacing: 0.5px;
  }
</style>
</head>
<body>
  <section class="front-panel">
    <p class="brand-name">Velmora Crest</p>
    <h1 class="product-title">DUAL-SIDED</h1>
    <p class="product-subtitle">MAGNIFYING MAKEUP MIRROR</p>
    <p class="magnification">3x magnified + 1x magnified</p>
    <p class="colour-variant">BLACK</p>
  </section>

  <section class="spine-panel">
    <div class="spine-title">
      <strong>DUAL-SIDED</strong>
      <span>MAGNIFYING MAKEUP MIRROR</span>
    </div>
    <span class="spine-brand">Velmora Crest</span>
  </section>
</body>
</html>
```